Business card design

I need my logo on this card, things I need the card to have on it
licensed and insured.
owner operators Milo & Trent Halvorsen
my phone number 5083716254
Disaster Recovery, Storm Damage Restoration, Proactive Disaster Plan Management, Roof Repair/Restoration Structural Repair and Reconstruction, Emergency Boarding and Tarping Service, Perimeter Fencing, Emergency Tree Removal,

```html
<!DOCTYPE html>
<html lang="en">
<head>
<meta charset="utf-8">
<title>Halvorsen's Construction L.L.C – Business Card</title>
<link href="https://fonts.googleapis.com/css2?family=Michroma&family=Montserrat:wght@400;700&display=swap" rel="stylesheet">
<style>
  :root {
    --backdrop: #dbd3ca;
    --card-blue: #3a95c0;
    --card-blue-deep: #2f87b3;
    --ink: #ffffff;
    --ink-faint: rgba(255, 255, 255, 0.14);
    --shadow: rgba(60, 50, 40, 0.25);
  }
  * { margin: 0; padding: 0; box-sizing: border-box; }
  html, body {
    width: 1200px;
    height: 800px;
    overflow: hidden;
    background: var(--backdrop);
  }
  .sheet {
    width: 1200px;
    height: 800px;
    display: flex;
    align-items: center;
    justify-content: center;
    gap: 40px;
  }
  .card {
    position: relative;
    width: 540px;
    height: 309px;
    background: linear-gradient(160deg, var(--card-blue) 0%, var(--card-blue-deep) 100%);
    color: var(--ink);
    overflow: hidden;
    box-shadow: 0 10px 24px var(--shadow);
    font-family: "Montserrat", sans-serif;
  }

  /* Shared company name treatment: one font, one weight, one colour */
  .company-name {
    font-family: "Montserrat", sans-serif;
    font-weight: 400;
    text-transform: uppercase;
    letter-spacing: 0.03em;
  }
  .brand-square {
    display: inline-block;
    background: var(--ink);
    flex: none;
  }

  /* Front */
  .brand-mini {
    position: absolute;
    left: 34px;
    top: 30px;
    display: flex;
    align-items: center;
    gap: 8px;
  }
  .brand-mini .brand-square { width: 12px; height: 12px; }
  .brand-mini .company-name { font-size: 10px; }

  .owners {
    position: absolute;
    left: 44px;
    top: 86px;
  }
  .owners .names {
    font-family: "Michroma", sans-serif;
    font-size: 17px;
    letter-spacing: 0.04em;
    text-transform: uppercase;
    white-space: nowrap;
  }
  .owners .role {
    font-weight: 700;
    font-size: 11.5px;
    margin-top: 6px;
  }
  .owners .phone,
  .owners .licence {
    font-weight: 400;
    font-size: 10.5px;
    margin-top: 2px;
  }
  .services {
    position: absolute;
    left: 58px;
    top: 172px;
    list-style: none;
    font-weight: 400;
    font-size: 10.5px;
    line-height: 1.38;
  }
  .faint-name {
    position: absolute;
    right: 26px;
    top: 178px;
    width: 200px;
    font-size: 24px;
    line-height: 1.15;
    text-align: right;
    color: var(--ink-faint);
  }

  /* Back */
  .card-back {
    display: flex;
    flex-direction: column;
    align-items: center;
    justify-content: center;
    gap: 18px;
  }
  .card-back .brand-square { width: 28px; height: 28px; }
  .card-back .company-name {
    font-size: 30px;
    line-height: 1.2;
    text-align: center;
  }
</style>
</head>
<body>
  <main class="sheet">
    <section class="card card-front" aria-label="Card front">
      <div class="brand-mini">
        <span class="brand-square"></span>
        <span class="company-name">Halvorsen's Construction L.L.C</span>
      </div>

      <div class="owners">
        <p class="names">Milo &amp; Trent Halvorsen</p>
        <p class="role">Owner Operator</p>
        <p class="phone">P: (508) 371-6254</p>
        <p class="licence">Licensed and Insured</p>
      </div>

      <ul class="services">
        <li>Disaster Recovery</li>
        <li>Perimeter Fencing</li>
        <li>Roof Repair/Restoration</li>
        <li>Emergency Tree Removal</li>
        <li>Storm Damage Restoration</li>
        <li>Proactive Disaster Plan Management</li>
        <li>Structural Repair and Reconstruction</li>
        <li>Emergency Boarding and Tarping Service</li>
      </ul>

      <p class="faint-name company-name" aria-hidden="true">Halvorsen's Construction</p>
    </section>

    <section class="card card-back" aria-label="Card back">
      <span class="brand-square"></span>
      <p class="company-name">Halvorsen's<br>Construction L.L.C</p>
    </section>
  </main>
</body>
</html>
```